Redesign website for small print company

Vindurgata is a small printing company in Iceland mainly servicing Students, schools, etc. We are also doing all kind of other jobs, like business cards, book printing, brochure printing etc. We are also selling books online.
Our website is: www.vindurgata.is
What we are looking for is:
- Web Design (Uncoded - PSD layout only)
- Mobile friendly design, using our current color scheme: Red, green, yellow and light gray.
- Clean simple design
- Simple, light and easy to use.
- More menu Items/drop down
Industry/Entity Type
Digital Printing
Number of Pages Required
5+ page
Requirements
Must have
- Easy navigation
- Designed for mobile
- Current color scheme (see logo)
Nice to have
- Icon based products

```html
<!DOCTYPE html>
<html lang="en">
<head>
<meta charset="utf-8">
<title>Vindurgata – Printing for students and schools</title>
<link href="https://fonts.googleapis.com/css2?family=Roboto:ital,wght@0,400;0,500;0,700;1,400;1,500&family=Lato:wght@400;700;900&display=swap" rel="stylesheet">
<style>
:root{
  --red:#e63232;
  --green:#1e6a37;
  --yellow:#f6d200;
  --cyan:#4cc3d9;
  --light:#efefef;
  --topbar:#f2f2f2;
  --dark:#262626;
  --footer:#232323;
  --text:#333;
  --muted:#555;
}
*{box-sizing:border-box;margin:0;padding:0}
html,body{width:1200px;height:3103px;overflow:hidden}
body{font-family:"Roboto",Arial,sans-serif;color:var(--text);background:#fff;position:relative}
section,header,footer,div{position:relative}
.abs{position:absolute}

/* top bar */
.topbar{height:41px;background:var(--topbar);font-size:12px;color:#333}
.topbar .info{position:absolute;top:0;height:41px;display:flex;align-items:center;gap:10px}
.topbar .info svg{width:14px;height:14px}
.lang{position:absolute;left:933px;top:0;width:124px;height:41px;background:#e2e2e2;display:flex;align-items:center;justify-content:center;gap:8px;font-size:12px}

/* header */
.header{height:71px;background:#fff}
.brand{position:absolute;left:141px;top:16px;display:flex;align-items:center;gap:10px}
.brand .mark{width:36px;height:36px;background:var(--red)}
.brand .name{font-weight:700;font-size:28px;color:#111;letter-spacing:.5px}
.nav{position:absolute;top:0;height:71px;display:flex;align-items:center;font-size:12px;font-weight:500;color:#222}
.nav a{position:absolute;white-space:nowrap;text-decoration:none;color:inherit}
.nav .active{color:var(--red)}
.dropdown{position:absolute;left:670px;top:89px;width:178px;background:#fff;box-shadow:0 3px 10px rgba(0,0,0,.18);z-index:5;font-size:12px}
.dropdown li{list-style:none;height:36px;line-height:36px;padding-left:14px;border-bottom:1px solid #ececec}

/* hero */
.hero{height:529px;background:radial-gradient(circle at 40% 45%,#9fe0ea 0%,var(--cyan) 45%,#3bb8d0 100%)}
.hero h1{position:absolute;left:141px;top:196px;font-family:"Lato",Arial,sans-serif;font-weight:400;font-size:42px;line-height:42px;color:#fff;letter-spacing:.5px}
.hero h1 b{font-weight:900}
.hero .visual{position:absolute;left:455px;top:140px;width:590px;height:245px;border-radius:4px;background:linear-gradient(90deg,#f1e6ee 0%,#f07a86 45%,#a556a6 75%,#6a3f8e 100%);opacity:.9}

/* section titles */
.title{position:absolute;left:0;width:1200px;text-align:center;font-weight:500;font-size:33px;color:#222}
.title span{color:var(--red)}
.divider{position:absolute;left:480px;width:240px;height:18px}
.divider:before,.divider:after{content:"";position:absolute;top:8px;width:105px;height:2px;background:#999}
.divider:before{left:0}.divider:after{right:0}
.divider i{position:absolute;left:112px;top:0;width:16px;height:16px;background:var(--yellow);border:3px solid var(--red)}

/* about */
.about{height:476px;background:#fff}
.about .copy{position:absolute;left:141px;top:178px;width:610px;font-size:12.5px;line-height:17px;color:#333}
.about .copy h3{font-size:16px;font-weight:500;color:#111;margin-bottom:10px}
.about .copy h3 span{color:var(--red)}
.about .copy p{margin-bottom:17px}
.about .badge{position:absolute;left:883px;top:180px;width:174px;height:224px;background:#f4f4f4;box-shadow:0 4px 10px rgba(0,0,0,.12);display:flex;align-items:center;justify-content:center;font-weight:700;font-size:24px;color:var(--green)}

/* products */
.products{height:656px;background:var(--light)}
.product{position:absolute;width:281px;height:194px;background:#f7f7f7;text-align:center}
.product.featured{background:#fff;box-shadow:0 4px 14px rgba(0,0,0,.18)}
.product .icon{position:absolute;left:100px;top:35px;width:80px;height:80px;border-radius:50%;background:#fff;border:2px solid #ddd;display:flex;align-items:center;justify-content:center}
.product .icon svg{width:40px;height:40px}
.product .label{position:absolute;left:0;top:128px;width:100%;font-size:17px;font-weight:500;color:#222}
.product.featured .label{color:var(--red)}

/* why */
.why{height:451px;background:linear-gradient(120deg,#2f2f2f 0%,#222 40%,#3a3634 70%,#262626 100%)}
.why .title{color:#fff}
.why .divider:before,.why .divider:after{background:#bbb}
.feature{position:absolute;width:420px;color:#fff}
.feature .ic{position:absolute;left:0;top:0;width:74px;height:74px;border-radius:50%;background:#fff;display:flex;align-items:center;justify-content:center}
.feature .ic svg{width:38px;height:38px}
.feature h4{position:absolute;left:90px;top:-2px;font-size:15px;font-weight:500;white-space:nowrap}
.feature p{position:absolute;left:90px;top:18px;width:325px;font-size:13px;line-height:17px;color:#ddd}

/* testimonials */
.testimonials{height:387px;background:#fff}
.quote{position:absolute;left:166px;top:156px;width:870px;text-align:center;font-style:italic;font-size:12.5px;line-height:23px;color:#333}
.author{position:absolute;left:0;top:232px;width:1200px;text-align:center;font-style:italic;font-weight:500;font-size:14px;color:var(--red)}
.avatar{position:absolute;left:569px;top:267px;width:60px;height:60px;background:linear-gradient(135deg,#6e6a63,#a79a8a);border:2px solid #ccc}
.dots{position:absolute;left:573px;top:350px;display:flex;gap:12px}
.dots i{width:9px;height:9px;border-radius:50%;background:#e3e3e3}
.dots i:first-child{background:var(--green)}
.arrow{position:absolute;top:211px;width:46px;height:65px;display:flex;align-items:center;justify-content:center}
.arrow.prev{left:74px;background:#e8e8e8}
.arrow.next{left:1080px;background:var(--green)}

/* newsletter */
.newsletter{height:87px;background:#ececec}
.newsletter .ic{position:absolute;left:140px;top:22px;width:42px;height:42px;border-radius:50%;border:2px solid #222;display:flex;align-items:center;justify-content:center}
.newsletter h5{position:absolute;left:199px;top:29px;font-size:22px;font-weight:400;color:#222;letter-spacing:.5px}
.newsletter .field{position:absolute;left:513px;top:29px;width:377px;height:29px;background:#fff;font-size:10px;color:#777;padding:9px 10px}
.newsletter .btn{position:absolute;left:904px;top:29px;width:153px;height:29px;background:var(--red);color:#fff;font-weight:700;font-size:14px;text-align:center;line-height:29px;letter-spacing:.5px}

/* footer */
.footer{height:356px;background:var(--footer);color:#fff}
.footer h6{position:absolute;top:62px;font-size:16px;font-weight:400;letter-spacing:.5px}
.input{position:absolute;left:141px;width:240px;background:#fff;color:#888;font-size:12px;padding:7px 8px}
.send{position:absolute;left:141px;top:259px;width:85px;height:25px;background:var(--red);font-size:12px;text-align:center;line-height:25px}
.map{position:absolute;left:455px;top:97px;width:296px;height:187px;background:linear-gradient(135deg,#d9dde0 0%,#cfe1ea 40%,#e4e6e2 70%,#b9d3e4 100%)}
.contact{position:absolute;left:824px;font-size:12.5px;line-height:17px;display:flex;gap:10px}
.contact svg{width:14px;height:14px;flex:none;margin-top:1px}
.legal{position:absolute;left:0;top:3054px;width:1200px;height:49px;background:var(--red);color:#fff;font-size:11px}
.legal p{position:absolute;left:141px;top:17px}
.pay{position:absolute;top:13px;width:38px;height:24px;background:#fff;border-radius:3px}
</style>
</head>
<body>

<div class="topbar">
  <div class="info" style="left:143px">
    <svg viewBox="0 0 24 24"><path fill="#1e6a37" d="M6.6 10.8a15 15 0 0 0 6.6 6.6l2.2-2.2c.3-.3.7-.4 1-.2 1.1.4 2.3.6 3.6.6.6 0 1 .4 1 1V20c0 .6-.4 1-1 1A17 17 0 0 1 3 4c0-.6.4-1 1-1h3.5c.6 0 1 .4 1 1 0 1.3.2 2.5.6 3.6.1.3 0 .7-.2 1z"/></svg>
    <span>555 0142</span>
  </div>
  <div class="info" style="left:381px">
    <svg viewBox="0 0 24 24"><path fill="#1e6a37" d="M2 5h20v14H2z"/><path d="M2 5l10 8 10-8" fill="none" stroke="#fff" stroke-width="2"/></svg>
    <span>verk@vindurgata.is</span>
  </div>
  <div class="info" style="left:672px">
    <svg viewBox="0 0 24 24"><circle cx="12" cy="12" r="9" fill="none" stroke="#1e6a37" stroke-width="3"/><path d="M12 7v5l3 2" stroke="#1e6a37" stroke-width="2" fill="none"/></svg>
    <span>Mon - Fri: 9-17</span>
  </div>
  <div class="lang">Language <svg width="10" height="6" viewBox="0 0 10 6"><path d="M0 0h10L5 6z" fill="#222"/></svg></div>
</div>

<header class="header">
  <div class="brand"><span class="mark"></span><span class="name">VINDURGATA</span></div>
  <nav class="nav">
    <a style="left:505px">HOME</a>
    <a style="left:575px">ABOUT US</a>
    <a class="active" style="left:670px">SERVICES <svg width="9" height="6" viewBox="0 0 9 6"><path d="M1 1l3.5 3.5L8 1" stroke="#e63232" stroke-width="1.6" fill="none"/></svg></a>
    <a style="left:776px">PRODUCTS</a>
    <a style="left:875px">JOB SUBMIT</a>
    <a style="left:983px">CONTACT US</a>
  </nav>
</header>

<ul class="dropdown">
  <li>Bookprinting</li>
  <li>Better Finances</li>
  <li>Photocopying</li>
  <li style="border:0">Spiral-bound books</li>
</ul>

<section class="hero">
  <h1><b>WE</b> HELP<br>YOUR<br><b>BUSINESS</b><br>COME TO LIFE</h1>
  <div class="visual" role="img" aria-label="Photo of printed business card samples"></div>
</section>

<section class="about">
  <h2 class="title" style="top:66px"><span>A</span>BOUT US</h2>
  <div class="divider" style="top:111px"><i></i></div>
  <div class="copy">
    <h3><span>W</span>elcome to University</h3>
    <p>University education is a company located in the campus, which has specialized in the service of school staff, as well as providing general public printing.</p>
    <p>Higher education publishes seminars and first-class textbooks for courses, prints theses for lesson, as well as working on an unprecedented number of smaller pieces for students, teachers and organizations. These include brochures, reports, questionnaires, business cards, books, OCR scanning and more.</p>
    <p>Higher education is a tailored print shop, The Green Leaf is the official eco-label of the Nordic countries, which has created a foothold in this country and is known among consumers.</p>
    <p>University education is located at the corner of Birkigata and Lindargata. (walked into Lindargötumegin)</p>
  </div>
  <div class="badge">Vindurgata</div>
</section>

<section class="products">
  <h2 class="title" style="top:65px"><span>O</span>UR PRODUCTS</h2>
  <div class="divider" style="top:112px"><i></i></div>

  <div class="product featured" style="left:141px;top:162px">
    <div class="icon"><svg viewBox="0 0 40 40" fill="none" stroke="#e63232" stroke-width="2"><path d="M10 4h16l6 6v26H10z"/><path d="M15 14h12M15 19h12M15 24h8"/><path d="M26 4v6h6"/></svg></div>
    <div class="label">ESSAYS</div>
  </div>
  <div class="product" style="left:459px;top:162px">
    <div class="icon"><svg viewBox="0 0 40 40" fill="none" stroke="#1e6a37" stroke-width="2"><rect x="5" y="9" width="30" height="22" rx="2"/><circle cx="14" cy="18" r="3"/><path d="M9 26c1-4 9-4 10 0M22 16h9M22 21h9M22 26h6"/></svg></div>
    <div class="label">BUSINESS CARDS</div>
  </div>
  <div class="product" style="left:778px;top:162px">
    <div class="icon"><svg viewBox="0 0 40 40" fill="none" stroke="#1e6a37" stroke-width="2"><path d="M5 9l10-3 10 3 10-3v25l-10 3-10-3-10 3z"/><path d="M15 6v25M25 9v25M8 15h4M18 15h4M28 15h4M8 20h4M18 20h4M28 20h4"/></svg></div>
    <div class="label">LEAFLETS</div>
  </div>
  <div class="product" style="left:141px;top:391px">
    <div class="icon"><svg viewBox="0 0 40 40" fill="none" stroke="#1e6a37" stroke-width="2"><path d="M11 5h18v30H11z"/><path d="M8 8v30h18M15 11h10M15 16h10M15 21h10M15 26h6"/></svg></div>
    <div class="label">BOOK PRINTING</div>
  </div>
  <div class="product" style="left:459px;top:391px">
    <div class="icon"><svg viewBox="0 0 40 40" fill="none" stroke="#1e6a37" stroke-width="2"><rect x="9" y="4" width="22" height="32"/><path d="M13 24l5-6 4 4 3-3 3 5z" fill="#1e6a37"/><path d="M13 9h14M13 13h14M13 29h14"/></svg></div>
    <div class="label">POSTERS</div>
  </div>
  <div class="product" style="left:778px;top:391px">
    <div class="icon"><svg viewBox="0 0 40 40" fill="none" stroke="#1e6a37" stroke-width="2"><path d="M10 5h20v30H10z"/><path d="M14 5v30M18 11h8M18 15h8"/></svg></div>
    <div class="label">TEXTBOOKS</div>
  </div>
</section>

<section class="why" role="img" aria-label="Dark background photo of colour swatch fan">
  <h2 class="title" style="top:60px"><span>W</span>HY CHOOSE US ?</h2>
  <div class="divider" style="top:105px"><i></i></div>

  <div class="feature" style="left:141px;top:183px">
    <div class="ic"><svg viewBox="0 0 40 40"><path d="M6 14l14-7 14 7v14l-14 7-14-7z" fill="#1e6a37"/><path d="M6 14l14 7 14-7M20 21v14" stroke="#fff" stroke-width="2" fill="none"/></svg></div>
    <h4>Over 200k Orders Completed</h4>
    <p>It is a long established fact that a reader will be distracted by the readable content of a page when looking at its layout.</p>
  </div>
  <div class="feature" style="left:639px;top:183px">
    <div class="ic"><svg viewBox="0 0 40 40" fill="#1e6a37"><circle cx="20" cy="13" r="5"/><circle cx="10" cy="16" r="4"/><circle cx="30" cy="16" r="4"/><path d="M11 32c0-7 4-11 9-11s9 4 9 11z"/><path d="M2 30c0-5 3-9 8-9 2 0 3 1 4 2-2 2-3 5-3 7zM38 30c0-5-3-9-8-9-2 0-3 1-4 2 2 2 3 5 3 7z"/></svg></div>
    <h4>Great Customer Service</h4>
    <p>It is a long established fact that a reader will be distracted by the readable content of a page when looking at its layout.</p>
  </div>
  <div class="feature" style="left:141px;top:300px">
    <div class="ic"><svg viewBox="0 0 40 40"><path d="M6 15l7-8h14l7 8-14 18z" fill="#1e6a37"/><path d="M6 15h28M13 7l7 26 7-26M17 15l3-8 3 8" stroke="#fff" stroke-width="1.5" fill="none"/></svg></div>
    <h4>Superior Quality and Value</h4>
    <p>It is a long established fact that a reader will be distracted by the readable content of a page when looking at its layout.</p>
  </div>
  <div class="feature" style="left:639px;top:300px">
    <div class="ic"><svg viewBox="0 0 40 40"><circle cx="23" cy="20" r="13" fill="#1e6a37"/><path d="M23 12v8l5 4" stroke="#fff" stroke-width="2.5" fill="none"/><path d="M3 15h6M2 20h6M3 25h6" stroke="#1e6a37" stroke-width="2.5"/></svg></div>
    <h4>Fast Turnaround</h4>
    <p>It is a long established fact that a reader will be distracted by the readable content of a page when looking at its layout.</p>
  </div>
</section>

<section class="testimonials">
  <h2 class="title" style="top:64px"><span>C</span>LIENT TESTIMONIALS</h2>
  <div class="divider" style="top:110px"><i></i></div>
  <a class="arrow prev"><svg width="14" height="26" viewBox="0 0 14 26"><path d="M12 2L2 13l10 11" stroke="#bbb" stroke-width="2" fill="none"/></svg></a>
  <p class="quote">Lorem ipsum dolor sit amet, consectetur adipiscing elit, sed do eiusmod tempor incididunt ut labore et dolore magna aliqua. Ut enim &nbsp;veniam, quis nostrud exercitation ullamco laboris nisi ut aliquip ex ea commodo consequat. Duis aute irure dolor in reprehenderit in voluptate velit esse cillum dolore eu fugiat nulla pariatur. Excepteur sint occaecat cupidatat non proident, sunt in culpa qui officia .</p>
  <p class="author">- Sconsectetur adipiscing</p>
  <div class="avatar" role="img" aria-label="Client portrait photo"></div>
  <div class="dots"><i></i><i></i><i></i></div>
  <a class="arrow next"><svg width="14" height="26" viewBox="0 0 14 26"><path d="M2 2l10 11L2 24" stroke="#fff" stroke-width="2" fill="none"/></svg></a>
</section>

<section class="newsletter">
  <div class="ic"><svg width="22" height="16" viewBox="0 0 22 16"><rect x="1" y="1" width="20" height="14" fill="#222"/><path d="M1 1l10 8 10-8" stroke="#fff" stroke-width="1.6" fill="none"/></svg></div>
  <h5>SIGN UP FOR NEWSLETTER</h5>
  <div class="field">Enter your email here</div>
  <div class="btn">SUBSCRIBE</div>
</section>

<footer class="footer">
  <h6 style="left:141px">DROP US A LINE</h6>
  <div class="input" style="top:97px;height:29px">Name</div>
  <div class="input" style="top:137px;height:29px">Email</div>
  <div class="input" style="top:176px;height:68px">Message</div>
  <div class="send">SEND</div>

  <h6 style="left:457px">LOCATION MAP</h6>
  <div class="map" role="img" aria-label="Street map showing the shop location">
    <svg class="abs" style="left:98px;top:62px" width="20" height="28" viewBox="0 0 20 28"><path d="M10 0a10 10 0 0 1 10 10c0 7-10 18-10 18S0 17 0 10A10 10 0 0 1 10 0z" fill="#e63232"/><circle cx="10" cy="10" r="3.5" fill="#fff"/></svg>
  </div>

  <h6 style="left:824px">FIND US</h6>
  <div class="contact" style="top:99px">
    <svg viewBox="0 0 20 28"><path d="M10 0a10 10 0 0 1 10 10c0 7-10 18-10 18S0 17 0 10A10 10 0 0 1 10 0z" fill="#e63232"/><circle cx="10" cy="10" r="3.5" fill="#232323"/></svg>
    <span>48 Harbor Lane<br>Lakeview, Oregon 97630</span>
  </div>
  <div class="contact" style="top:141px">
    <svg viewBox="0 0 24 24"><path fill="#e63232" d="M6.6 10.8a15 15 0 0 0 6.6 6.6l2.2-2.2c.3-.3.7-.4 1-.2 1.1.4 2.3.6 3.6.6.6 0 1 .4 1 1V20c0 .6-.4 1-1 1A17 17 0 0 1 3 4c0-.6.4-1 1-1h3.5c.6 0 1 .4 1 1 0 1.3.2 2.5.6 3.6.1.3 0 .7-.2 1z"/></svg>
    <span>555 0142</span>
  </div>
  <div class="contact" style="top:172px">
    <svg viewBox="0 0 24 24"><path fill="#e63232" d="M2 5h20v14H2z"/><path d="M2 5l10 8 10-8" fill="none" stroke="#232323" stroke-width="2"/></svg>
    <span>verk@vindurgata.is</span>
  </div>
  <div class="abs" style="left:824px;top:212px;width:16px;height:16px;background:#ddd"></div>
</footer>

<div class="legal">
  <p>Copyright © 2018 Vindurgata. All Rights Reserved</p>
  <span class="pay" style="left:975px"></span>
  <span class="pay" style="left:1019px"></span>
</div>

</body>
</html>
```